Business Card Design

We are a company that provides stump grinding services for residential and commercial clients. Looking for a simple business card design that may have some type of graphic on the card that will tie in with the Tamsen name(Grizzly Bear, Paw Print, etc) . Possibly some foliage wrapping around part of the card? Would like to have a simple design that stands out because it is unique. We are working on getting the website set up and there is a simple graphic on the top of the page that came to mind when I mentioned the leaves.

Industry/Entity Type

Business

Contact Information for Business Card

Tamsen Stump Grinding 303-257-4788KodiakStumps.Com

Font styles to use
Serif

Requirements
Must have
• Business name
• Website Address
• Phone Number
Nice to have
• Graphics that would be associated with a Tamsen bear.
Should not have
• Nothing frilly

```html
<!DOCTYPE html>
<html lang="en">
<head>
<meta charset="utf-8">
<title>Tamsen Stump Grinding — Business Card</title>
<link rel="stylesheet" href="https://fonts.googleapis.com/css2?family=Lato:wght@400;700&display=swap">
<style>
  :root {
    --page-bg: #d9d9d9;
    --card-black: #0b0b0c;
    --card-glow: #232427;
    --brand-blue: #5b8fd6;
    --text-light: #eef0f3;
    --mark-fill: #ffffff;
  }

  * { margin: 0; padding: 0; box-sizing: border-box; }

  html, body {
    width: 1200px;
    height: 900px;
    overflow: hidden;
    background: var(--page-bg);
  }

  .stage {
    width: 1200px;
    height: 900px;
    display: flex;
    align-items: center;
    justify-content: center;
  }

  .business-card {
    position: relative;
    width: 980px;
    height: 560px;
    background: radial-gradient(ellipse at 45% 35%, var(--card-glow) 0%, var(--card-black) 70%);
    box-shadow: 0 10px 30px rgba(0, 0, 0, 0.25);
    font-family: "Lato", sans-serif;
  }

  .brand {
    position: absolute;
    left: 390px;
    top: 130px;
    display: flex;
    align-items: center;
    gap: 22px;
  }

  .brand-dot {
    width: 118px;
    height: 118px;
    border-radius: 50%;
    background: var(--mark-fill);
    flex: none;
  }

  .brand-name {
    color: var(--brand-blue);
    font-weight: 700;
    font-size: 40px;
    line-height: 1.15;
    letter-spacing: 1px;
    text-transform: uppercase;
  }

  .brand-name span { display: block; }

  .contact {
    position: absolute;
    left: 130px;
    top: 340px;
    list-style: none;
    color: var(--text-light);
    font-size: 28px;
    line-height: 1.3;
  }

  .contact li {
    display: flex;
    align-items: center;
    gap: 14px;
  }

  .contact svg {
    width: 22px;
    height: 22px;
    fill: none;
    stroke: var(--brand-blue);
    stroke-width: 2.2;
    flex: none;
  }

  .contact .icon-phone { fill: var(--brand-blue); stroke: none; }
</style>
</head>
<body>
  <main class="stage">
    <section class="business-card" aria-label="Tamsen Stump Grinding business card">
      <div class="brand">
        <div class="brand-dot" aria-hidden="true"></div>
        <h1 class="brand-name"><span>Tamsen Stump</span><span>Grinding</span></h1>
      </div>

      <ul class="contact">
        <li>
          <svg class="icon-phone" viewBox="0 0 24 24" aria-hidden="true">
            <path d="M3 9c0-3 4-5 9-5s9 2 9 5l-1 2h-4l-1-3H9L8 11H4z"/>
            <rect x="6" y="12" width="12" height="8" rx="2"/>
          </svg>
          <span>303-555-0146</span>
        </li>
        <li>
          <svg viewBox="0 0 24 24" aria-hidden="true">
            <path d="M10 14l4-4"/>
            <path d="M8 12l-3 3a3 3 0 0 0 4 4l3-3"/>
            <path d="M16 12l3-3a3 3 0 0 0-4-4l-3 3"/>
          </svg>
          <span>TamsenStumps.Com</span>
        </li>
      </ul>
    </section>
  </main>
</body>
</html>
```